Pop punk gig poster design!

In need of an amazing poster design for a gig We are organising, the genre is pop punk, and will be an all ages gig. I need to it bold, random and capture the eye of any bypasses, and make people want to go to the gig just because the poster is awesome! The event will be called "The great daydream" and will consist of three bands and an acoustic set to open. All the bands are full of energy and create an unreal ambiance during there shows, I would like to capture that in the poster. Open to anything spectacular, the sky is the limit.

• I need to have the name of the event "The Great Daydream"
Band names(in this order):
-Fold the Kite
-Velvet Tuesday
-Milo's Compass
-Tessaly Grovers

Date: Saturday 10th November 2012
Time: 5:15pm
Venue: The Quill, 74 Marrowby street, West End, QLD 4101
Ticket price: $10+bf online
$15 at the door.
Free BBQ

```html
<!DOCTYPE html>
<html lang="en">
<head>
<meta charset="utf-8">
<title>The Great Daydream</title>
<link rel="stylesheet" href="https://fonts.googleapis.com/css2?family=Audiowide&family=Pirata+One&family=Metamorphous&family=Russo+One&family=Days+One&display=swap">
<style>
  :root {
    --wall-light: #eceac0;
    --wall-mid: #cfcd98;
    --wall-dark: #7f7f52;
    --wall-base: #5c5c3c;
    --ink: #1c1a38;
    --guitar: #4c4672;
    --guitar-dark: #35305a;
    --band-fill: #ddd4a4;
    --band-edge: #141218;
    --rock-ink: #3b2840;
    --rock-glow: #d27ab0;
    --detail-ink: #fffbe8;
    --detail-shadow: #1a1810;
  }
  * { margin: 0; padding: 0; box-sizing: border-box; }
  html, body { width: 848px; height: 1200px; overflow: hidden; background: var(--wall-mid); }
  .poster {
    position: relative;
    width: 848px;
    height: 1200px;
    overflow: hidden;
  }
  .brick-wall {
    position: absolute; inset: 0;
    background:
      linear-gradient(180deg, rgba(0,0,0,0) 0%, rgba(0,0,0,0) 78%, rgba(60,58,36,0.55) 88%, rgba(50,48,30,0.75) 100%),
      radial-gradient(ellipse at 45% 40%, var(--wall-light) 0%, var(--wall-mid) 55%, var(--wall-dark) 100%);
  }
  .skyline-strip {
    position: absolute;
    left: 35px; top: 4px;
    width: 785px; height: 58px;
    background: linear-gradient(180deg, #2a2650 0%, #3a3566 100%);
    opacity: 0.85;
  }
  .event-title {
    position: absolute;
    left: 0; top: 76px;
    width: 848px;
    text-align: center;
    font-family: "Audiowide", sans-serif;
    font-size: 58px;
    letter-spacing: 2px;
    color: var(--ink);
    text-transform: uppercase;
    white-space: nowrap;
  }
  .title-rule {
    position: absolute;
    left: 0; top: 142px;
    width: 848px; height: 3px;
    background: var(--ink);
    opacity: 0.7;
  }
  .guitar-silhouette {
    position: absolute;
    left: -40px; top: 560px;
    width: 980px; height: 260px;
    border-radius: 130px 40px 40px 130px;
    background: linear-gradient(180deg, var(--guitar) 0%, var(--guitar-dark) 100%);
    transform: rotate(-34deg);
    transform-origin: center;
    opacity: 0.95;
  }
  .tagline {
    position: absolute;
    left: 20px; top: 190px;
    font-family: "Pirata One", cursive;
    font-size: 72px;
    color: var(--rock-ink);
    text-transform: uppercase;
    letter-spacing: 5px;
    transform: rotate(10deg);
    transform-origin: left top;
    text-shadow: 3px 3px 0 var(--rock-glow), -1px -1px 0 var(--rock-glow);
    white-space: nowrap;
  }
  .lineup {
    position: absolute;
    left: 290px; top: 355px;
    list-style: none;
    transform: rotate(9deg);
    transform-origin: left top;
  }
  .lineup li {
    font-family: "Metamorphous", serif;
    font-size: 50px;
    line-height: 96px;
    color: var(--band-fill);
    text-transform: uppercase;
    white-space: nowrap;
    text-shadow:
      2px 2px 0 var(--band-edge), -2px -2px 0 var(--band-edge),
      2px -2px 0 var(--band-edge), -2px 2px 0 var(--band-edge),
      5px 5px 6px var(--band-edge);
  }
  .tickets {
    position: absolute;
    right: 8px; top: 872px;
    text-align: right;
    font-family: "Russo One", sans-serif;
    font-style: italic;
    font-size: 30px;
    color: var(--ink);
    text-transform: uppercase;
    letter-spacing: 1px;
  }
  .tickets p {
    line-height: 40px;
    border-bottom: 1px solid rgba(28, 26, 56, 0.5);
    padding-right: 4px;
  }
  .tickets .extra {
    font-size: 26px;
    line-height: 38px;
    border-bottom: none;
  }
  .gig-details {
    position: absolute;
    left: 35px; top: 1012px;
    font-family: "Days One", sans-serif;
    font-size: 25px;
    line-height: 44px;
    color: var(--detail-ink);
    text-transform: uppercase;
    text-shadow:
      2px 2px 0 var(--detail-shadow), -1px -1px 0 var(--detail-shadow),
      1px -1px 0 var(--detail-shadow), -1px 1px 0 var(--detail-shadow),
      2px 3px 6px rgba(0, 0, 0, 0.8);
  }
</style>
</head>
<body>
  <main class="poster">
    <div class="brick-wall" role="img" aria-label="Weathered pale brick wall background"></div>
    <div class="skyline-strip" role="img" aria-label="Row of small city and festival icons"></div>

    <h1 class="event-title">The Great Daydream</h1>
    <div class="title-rule"></div>

    <div class="guitar-silhouette" role="img" aria-label="Textured electric guitar silhouette"></div>

    <p class="tagline">Let us rock....</p>

    <ul class="lineup">
      <li>Fold the Kite</li>
      <li>Velvet Tuesday</li>
      <li>Milo's Compass</li>
      <li>Tessaly Grovers</li>
    </ul>

    <div class="tickets">
      <p>Ticket price: $10+bf online</p>
      <p>$15 at the door</p>
      <p class="extra">Free BBQ</p>
    </div>

    <div class="gig-details">
      <p>Date: Saturday 10th November 2012</p>
      <p>Time: 5:15pm</p>
      <p>Venue: The Quill, 74 Marrowby Street,</p>
      <p>West End, QLD 4101</p>
    </div>
  </main>
</body>
</html>
```